BRANDEMEIER & BRANDEMEIER,LLP NEEDS A NEW LETTERHEAD DESIGN

a conservative yet contemporary layout befitting a long established
firm, consistent with the times, some form of logo so it catches ones attention, and is
admirable, but portrays integrity
Updates

I would like to approve #22066987 Please advise how to do this as it’s confusing on the site so I can approve payment for the designer

Target Market(s)

real estate investors and building management people

Industry/Entity Type

Law Firm

Font styles to use
Serif

Colors

Designer to choose colors to be used in the design.

Requirements
Must have
• some form of conservative logo

```html
<!DOCTYPE html>
<html lang="en">
<head>
<meta charset="utf-8">
<title>Brandemeier &amp; Brandemeier LLP – Letterhead</title>
<link rel="stylesheet" href="https://fonts.googleapis.com/css2?family=Marcellus+SC&family=Roboto:wght@300;400&display=swap">
<style>
  :root {
    --backdrop: #cbccd1;
    --paper: #f2f2f2;
    --ink: #6a6a6a;
    --ink-dark: #4f4f4f;
    --brand-blue: #1e88d0;
    --rule: #9a9a9a;
  }
  * { margin: 0; padding: 0; box-sizing: border-box; }
  html, body {
    width: 1200px; height: 1166px; overflow: hidden;
    background: var(--backdrop);
  }
  .letterhead {
    position: absolute; left: 173px; top: 33px;
    width: 853px; height: 1100px;
    background: var(--paper);
    font-family: "Roboto", "Helvetica Neue", Arial, sans-serif;
    font-weight: 300;
    color: var(--ink);
  }
  .brand-mark {
    position: absolute; left: 76px; top: 62px;
    width: 64px; height: 64px;
  }
  .brand-name {
    position: absolute; left: 164px; top: 68px;
    font-family: "Marcellus SC", "Trajan Pro", serif;
    font-size: 24px; letter-spacing: 0.2px;
    color: var(--ink-dark); white-space: nowrap;
  }
  .brand-rule {
    position: absolute; left: 164px; top: 99px;
    width: 359px; height: 1px; background: var(--rule);
  }
  .brand-tagline {
    position: absolute; left: 164px; top: 105px;
    font-family: "Marcellus SC", "Trajan Pro", serif;
    font-size: 11px; letter-spacing: 5.1px;
    color: var(--ink); white-space: nowrap;
  }
  .firm-contact {
    position: absolute; right: 76px; top: 70px;
    text-align: right; font-size: 11px; line-height: 17px;
    font-weight: 400; color: var(--ink);
  }
  .firm-contact .gap { height: 17px; }
  .firm-contact .label,
  .firm-contact .web { color: var(--brand-blue); }
  .recipient {
    position: absolute; left: 76px; top: 265px;
    font-size: 12.2px; line-height: 14.8px; font-weight: 400;
  }
  .letter-body {
    position: absolute; left: 76px; top: 392px; width: 701px;
    font-size: 12.1px; line-height: 14.7px;
    text-align: justify; letter-spacing: -0.15px;
  }
  .letter-body p { margin-bottom: 14.7px; }
  .closing {
    position: absolute; left: 76px; top: 757px;
    font-size: 12.2px; font-weight: 400;
  }
  .signature {
    position: absolute; left: 76px; top: 783px;
    width: 140px; height: 58px;
    background: linear-gradient(90deg, rgba(30,30,30,0.14), rgba(30,30,30,0.05));
    border-radius: 4px;
  }
  .signatory {
    position: absolute; left: 76px; top: 860px;
    font-size: 12.2px; line-height: 14.8px; font-weight: 400;
  }
</style>
</head>
<body>
  <main class="letterhead">
    <svg class="brand-mark" viewBox="0 0 64 64" aria-hidden="true">
      <circle cx="32" cy="32" r="30" fill="none" stroke="var(--brand-blue)" stroke-width="2.5"/>
    </svg>
    <div class="brand-name">Brandemeier &amp; Brandemeier LLP</div>
    <div class="brand-rule"></div>
    <div class="brand-tagline">ATTORNEYS AND COUNSELORS AT LAW</div>

    <address class="firm-contact">
      <div>48 Harbor Row Suite 210</div>
      <div>Brooklyn, New York 11201</div>
      <div class="gap"></div>
      <div><span class="label">T:</span> (718) 555-0142 · <span class="label">F:</span> (718)-555-0179</div>
      <div><span class="label">E:</span> office@bblawfirm.com · <span class="web">www.bblawfirm.com</span></div>
    </address>

    <div class="recipient">
      Mr. Everett Malloran<br>
      President and CEO<br>
      Northvale Systems LLC.<br>
      880 Lexington Avenue, Suite 3100<br>
      New York, NY 10065
    </div>

    <section class="letter-body">
      <p>Dear Mr. Malloran:</p>
      <p>As Chairperson of the Corporate Conscience Campaign - Helping the Homeless in New York, I am writing this to thank you personally for your company's support in last month's fund-raising effort.</p>
      <p>As I indicated when we spoke on the phone two weeks ago, the campaign was considered a resounding success, raising a total of $1.65 million to-date, significantly exceeding our target of $1 million. Some donations are still trickling in, so we could end up close to a total of $2 million.</p>
      <p>Northvale Systems was an influential leader throughout the entire three-month campaign. In fact, we couldn't have succeeded without the generous support of your company, both financially, and through your organizational and administrative assistance. Your Team Leader, Denise Arvello was particularly impressive, going above and beyond what we could have expected of someone performing as a volunteer while continuing on with her day-to-day duties. Please convey my special thanks to Denise.</p>
      <p>I would also ask you to convey my sincere thanks and congratulations to all of those other people in your company who contributed in any way to the Helping the Homeless Campaign. Please tell them that the sum of their contributions resulted in a major success that they should all be proud of taking part in.</p>
      <p>I believe that the 27 companies that participated in this effort have set a new standard for social responsibility in this community, and have set a powerful example that will inspire other companies and organizations to do the same.</p>
      <p>I look forward to seeing you at the Mayor's special thank you reception next month.</p>
    </section>

    <div class="closing">Yours sincerely,</div>
    <div class="signature" role="img" aria-label="Handwritten signature of the fundraising chair"></div>
    <div class="signatory">
      Harold Brenning<br>
      Fundraising Chair
    </div>
  </main>
</body>
</html>
```